TLK Electricial Contracting Services

Hi guys, after a design for my small electrical company, have logo design files to be incorporated into the layout, the basic concept is electrical contracting services for residential, commercial, industrial & data services, image is clean clear and strong,

Card format is to have a nice clean logo on front,with maybe the Residential – commercial – industrial - data, followed with licensed & insured, followed by contact details on backside of the card.

Target Market(s)

Residential, commercial, industrial sectors.

Industry/Entity Type

Electrical

Contact Information for Business Card

TLK logo,
Residential – commercial – industrial - data
REC: 61307
Email: tlk@vornamail.net.au
Phone: 0487 352 019

Requirements
Must have
• Clean & strong design.
Nice to have
• If possible, I would like the logo colours inverted so the text is orange and the background is black on the front of the card, then the backside of the card be the reverse colour
Should not have
• No Sparks, lightning bolts,

```html
<!DOCTYPE html>
<html lang="en">
<head>
<meta charset="utf-8">
<title>TLK Electrical – Business Card</title>
<link rel="stylesheet" href="https://fonts.googleapis.com/css2?family=Open+Sans:wght@400;600;700;800&display=swap">
<style>
  :root {
    --orange: #f5832a;
    --white: #ffffff;
    --ink: #2b2b2b;
    --rule: #cfcfcf;
    --bg-top: #262626;
    --bg-bottom: #030303;
  }
  html, body {
    margin: 0;
    padding: 0;
    width: 1200px;
    height: 900px;
    overflow: hidden;
  }
  body {
    background: linear-gradient(180deg, var(--bg-top) 0%, #151515 55%, var(--bg-bottom) 100%);
    font-family: "Open Sans", Arial, sans-serif;
    position: relative;
  }
  .card {
    position: absolute;
    box-sizing: border-box;
  }
  .card--contact {
    left: 122px;
    top: 75px;
    width: 541px;
    height: 328px;
    background: var(--white);
    border-radius: 64px 0 64px 0;
  }
  .card--brand {
    left: 520px;
    top: 464px;
    width: 520px;
    height: 314px;
    background: var(--orange);
    border-radius: 0 64px 0 64px;
  }
  .brand {
    position: absolute;
    text-align: right;
    line-height: 1;
  }
  .brand__mark {
    display: block;
    font-weight: 800;
    letter-spacing: -2px;
  }
  .brand__name {
    display: block;
    font-weight: 700;
  }
  .card--contact .brand {
    right: 37px;
    top: 22px;
    color: var(--orange);
  }
  .card--contact .brand__mark { font-size: 88px; }
  .card--contact .brand__name { font-size: 15px; margin-top: -2px; }
  .card--brand .brand {
    left: 122px;
    top: 82px;
    width: 252px;
    color: var(--white);
  }
  .card--brand .brand__mark { font-size: 108px; }
  .card--brand .brand__name { font-size: 17px; margin-top: -6px; }
  .services {
    position: absolute;
    left: 0;
    right: 0;
    top: 222px;
    margin: 0;
    text-align: center;
    color: var(--white);
    font-size: 13px;
    font-weight: 600;
    line-height: 20px;
  }
  .services__licence {
    display: block;
    font-weight: 400;
  }

  .person {
    position: absolute;
    left: 35px;
    top: 134px;
    right: 22px;
  }
  .person__name {
    margin: 0;
    font-size: 22px;
    font-weight: 600;
    color: var(--orange);
    line-height: 1.2;
  }
  .person__role {
    display: flex;
    align-items: center;
    font-size: 14px;
    color: var(--ink);
    line-height: 1.2;
  }
  .person__role::after {
    content: "";
    flex: 1;
    height: 1px;
    background: var(--rule);
    margin-left: 2px;
    margin-top: 2px;
  }
  .contacts {
    position: absolute;
    right: 36px;
    top: 183px;
    margin: 0;
    padding: 0;
    list-style: none;
  }
  .contacts li {
    display: flex;
    justify-content: flex-end;
    align-items: center;
    height: 23px;
    font-size: 15px;
    color: var(--ink);
  }
  .contacts svg {
    width: 11px;
    height: 11px;
    margin-left: 9px;
    fill: var(--orange);
    flex: none;
  }
</style>
</head>
<body>

<section class="card card--contact">
  <div class="brand">
    <span class="brand__mark">TLK</span>
    <span class="brand__name">Tarlo Kane Electrical</span>
  </div>
  <div class="person">
    <h1 class="person__name">Daniel Hart</h1>
    <div class="person__role">Managing Director</div>
  </div>
  <ul class="contacts">
    <li>0487 352 019
      <svg viewBox="0 0 12 12" aria-hidden="true"><path d="M1 4c0-2 2-3 5-3s5 1 5 3v1H8V4H4v1H1z"/><rect x="2" y="6" width="8" height="5" rx="1"/></svg>
    </li>
    <li>REC: 61307
      <svg viewBox="0 0 12 12" aria-hidden="true"><rect x="1" y="2" width="10" height="8" rx="1"/></svg>
    </li>
    <li>Licensed &amp; Insured
      <svg viewBox="0 0 12 12" aria-hidden="true"><path d="M2 6.5l2.5 2.5L10 3" fill="none" stroke="#f5832a" stroke-width="1.8" stroke-linecap="round"/></svg>
    </li>
    <li>tlk@vornamail.net.au
      <svg viewBox="0 0 12 12" aria-hidden="true"><path d="M1 3h10v6H1z M1 3l5 3.5L11 3" fill="none" stroke="#f5832a" stroke-width="1.4"/></svg>
    </li>
    <li>www.tlkelectrical.net.au
      <svg viewBox="0 0 12 12" aria-hidden="true"><path d="M5 7l2-2M4 6L2.5 7.5a1.8 1.8 0 0 0 2.5 2.5L6.5 8.5M8 6l1.5-1.5a1.8 1.8 0 0 0-2.5-2.5L5.5 3.5" fill="none" stroke="#f5832a" stroke-width="1.4" stroke-linecap="round"/></svg>
    </li>
  </ul>
</section>

<section class="card card--brand">
  <div class="brand">
    <span class="brand__mark">TLK</span>
    <span class="brand__name">Tarlo Kane Electrical</span>
  </div>
  <p class="services">Residential – Commercial – Industrial – Data
    <span class="services__licence">Licensed &amp; Insured · REC: 61307</span>
  </p>
</section>

</body>
</html>
```